Business card design needed

Our company background is that we provides transfers to and from the airport, social & corporate events, weddings.
We are also available for charter for birthday party, wine tastings, concerts, anniversary, school balls etc.
Our business cards have to reflect that we have a professional company, they are our first contact and have to stand out from the other 'players' in the market.

Industry/Entity Type

School

Contact Information for Business Card

TELVIK BDR, Lorcan & Mirabel, mob: 0428 351 972, PO Box 847, Kwinana WA 6971, ABN 52 714 309 268, Lic 7164/2918,

Requirements
Must have
• Telephone number: 0428 351 972
Website: www.TELVIKBDR.com.au
postal address: PO Box 847, Kwinana WA 6971
Licences: Lic 7164/2918

***If using the new photo (one with the bus and buildings behind it), if possible can the buildings be cropped out. Thanks
Nice to have
• would be nice to have the pics of the vehicle(s), preferred the Vorn on the card but not too fussed.
Should not have
• Picture of vehicle we don't have in our fleet. (We ONLY have the Vornelles and Korimu Daltra mini bus)

```html
<!DOCTYPE html>
<html lang="en">
<head>
<meta charset="utf-8">
<title>TELVIK BDR Business Card</title>
<link rel="stylesheet" href="https://fonts.googleapis.com/css2?family=Open+Sans:wght@400;700&display=swap">
<style>
  :root {
    --backdrop: #e9e6e1;
    --card-black: #0b0b0b;
    --card-sheen: #3a3a3a;
    --text-white: #f4f4f4;
    --text-soft: #d6d6d6;
    --photo-light: #f2f3f4;
    --photo-mid: #c9ccd0;
    --photo-dark: #5d6165;
    --photo-green: #55604a;
  }
  html, body {
    margin: 0;
    width: 1200px;
    height: 964px;
    overflow: hidden;
    background: var(--backdrop);
    font-family: "Open Sans", sans-serif;
  }
  .stage {
    width: 1200px;
    height: 964px;
    display: flex;
    align-items: center;
    justify-content: center;
  }
  .business-card {
    position: relative;
    width: 1000px;
    height: 556px;
    overflow: hidden;
    border-radius: 4px;
    background:
      radial-gradient(ellipse 70% 60% at 30% 55%, var(--card-sheen) 0%, transparent 70%),
      linear-gradient(160deg, #202020 0%, var(--card-black) 70%);
    box-shadow: 0 18px 40px rgba(0,0,0,0.35);
    color: var(--text-white);
  }
  .vehicle-photo {
    position: absolute;
    top: 0;
    left: 360px;
    width: 640px;
    height: 300px;
  }
  .identity {
    position: absolute;
    left: 60px;
    top: 222px;
  }
  .company-name {
    margin: 0;
    font-weight: 700;
    font-size: 40px;
    letter-spacing: 1px;
    line-height: 1.1;
  }
  .owners, .mobile {
    margin: 2px 0 0;
    font-size: 30px;
    font-weight: 400;
    line-height: 1.2;
  }
  .postal-details {
    margin: 20px 0 0 70px;
    font-size: 16px;
    line-height: 1.5;
    color: var(--text-soft);
    font-style: normal;
  }
  .services {
    position: absolute;
    right: 40px;
    bottom: 44px;
    width: 620px;
    margin: 0;
    font-size: 16px;
    line-height: 1.55;
    white-space: nowrap;
    color: var(--text-white);
  }
</style>
</head>
<body>
<main class="stage">
  <section class="business-card">
    <svg class="vehicle-photo" viewBox="0 0 640 300" role="img" aria-label="Photo of the white company minibus">
      <defs>
        <linearGradient id="vehicleTone" x1="0" y1="0" x2="1" y2="1">
          <stop offset="0" stop-color="var(--photo-green)"/>
          <stop offset="0.25" stop-color="var(--photo-light)"/>
          <stop offset="0.6" stop-color="var(--photo-mid)"/>
          <stop offset="1" stop-color="var(--photo-dark)"/>
        </linearGradient>
      </defs>
      <polygon points="160,0 640,0 640,300 0,300" fill="url(#vehicleTone)"/>
    </svg>

    <div class="identity">
      <h1 class="company-name">TELVIK BDR</h1>
      <p class="owners">Lorcan &amp; Mirabel</p>
      <p class="mobile">mob: 0428 351 972</p>
      <address class="postal-details">
        PO Box 847,<br>
        Kwinana WA 6971,<br>
        ABN 52 714 309 268,<br>
        Lic 7164/2918<br>
        www.TELVIKBDR.com.au
      </address>
    </div>

    <p class="services">Transfers to and from the airport, social &amp; corporate events, weddings<br>charter for birthday party, wine tastings, concerts, anniversary, school balls etc.</p>
  </section>
</main>
</body>
</html>
```